Dalvick's Business Card

I need some designs for a new business card including the new logo attached. An old example of our business card is also attached to show all the data that should be included on the new design.
**I added some more examples someone had mocked up**

Contact Information for Business Card

Should include all info on other examples uploaded.

```html
<!DOCTYPE html>
<html lang="en">
<head>
<meta charset="utf-8">
<title>Dalvick's Business Card</title>
<link href="https://fonts.googleapis.com/css2?family=Poppins:ital,wght@0,400;0,500;0,600;1,400&family=Montserrat:wght@600;700&display=swap" rel="stylesheet">
<style>
  :root {
    --backdrop: #b7b7b7;
    --brand-blue: #0273bd;
    --brand-red: #ec1c24;
    --ink: #111111;
    --paper: #ffffff;
  }
  * { box-sizing: border-box; margin: 0; padding: 0; }
  html, body { width: 1200px; height: 1200px; overflow: hidden; }
  body {
    background: var(--backdrop);
    font-family: "Poppins", sans-serif;
    position: relative;
  }
  .card {
    position: absolute;
    top: 303px;
    height: 594px;
  }
  .card-front {
    left: 200px;
    width: 369px;
  }
  .front-artwork {
    width: 100%;
    height: 100%;
    background: linear-gradient(100deg, var(--brand-red) 0%, var(--brand-red) 30%, #f3f3f3 40%, var(--brand-blue) 52%, var(--brand-blue) 100%);
  }
  .card-back {
    left: 599px;
    width: 364px;
    background: var(--paper);
    text-align: center;
  }
  .brand {
    position: absolute;
    top: 112px;
    left: 0;
    width: 100%;
    display: flex;
    flex-direction: column;
    align-items: center;
  }
  .brand-row {
    display: flex;
    align-items: center;
    gap: 10px;
  }
  .brand-dot {
    width: 34px;
    height: 34px;
    border-radius: 50%;
    background: var(--brand-red);
  }
  .brand-name {
    font-family: "Montserrat", sans-serif;
    font-weight: 700;
    font-size: 38px;
    letter-spacing: 1px;
    color: var(--brand-blue);
    line-height: 1;
  }
  .brand-tagline {
    margin-top: 6px;
    font-family: "Montserrat", sans-serif;
    font-weight: 600;
    font-size: 9.5px;
    color: var(--brand-red);
    letter-spacing: 0.2px;
  }
  .person-name {
    position: absolute;
    top: 256px;
    width: 100%;
    font-weight: 600;
    font-size: 23px;
    color: var(--brand-blue);
  }
  .name-rule {
    position: absolute;
    top: 295px;
    left: 135px;
    width: 94px;
    height: 1.5px;
    background: var(--brand-blue);
  }
  .contact {
    position: absolute;
    top: 307px;
    width: 100%;
    font-size: 17px;
    line-height: 24px;
    color: var(--ink);
  }
  .band {
    position: absolute;
    left: 0;
    width: 100%;
    color: var(--paper);
    font-weight: 500;
    font-size: 16.5px;
    display: flex;
    flex-direction: column;
    justify-content: center;
  }
  .band-credentials {
    top: 365px;
    height: 67px;
    background: var(--brand-blue);
    line-height: 24px;
    font-weight: 600;
  }
  .service-area {
    position: absolute;
    top: 446px;
    width: 100%;
    font-style: italic;
    font-size: 16.5px;
    line-height: 22px;
    color: var(--ink);
  }
  .band-call {
    top: 510px;
    height: 84px;
    background: var(--brand-red);
    line-height: 22px;
  }
</style>
</head>
<body>
  <section class="card card-front">
    <div class="front-artwork" role="img" aria-label="Large brand symbol artwork in red, white and blue filling the card front"></div>
  </section>

  <section class="card card-back">
    <div class="brand">
      <div class="brand-row">
        <span class="brand-dot"></span>
        <span class="brand-name">DALVICK'S</span>
      </div>
      <div class="brand-tagline">AIR CONDITIONING &amp; HEATING SERVICE</div>
    </div>

    <h1 class="person-name">MARK DALVICK</h1>
    <div class="name-rule"></div>
    <div class="contact">
      <p>555.014.2870</p>
      <p>hello@dalvickhvac.com</p>
    </div>

    <div class="band band-credentials">
      <p>LICENSED &amp; INSURED</p>
      <p>FAMILY OWNED &amp; OPERATED</p>
    </div>

    <div class="service-area">
      <p>Serves Brookfield</p>
      <p>IA &amp; Surrounding Areas</p>
    </div>

    <div class="band band-call">
      <p>CALL TODAY FOR ALL YOUR HVAC</p>
      <p>REFRIGERATION &amp; PLUMBING NEEDS</p>
    </div>
  </section>
</body>
</html>
```